indépendant en tant que Massothérapeute et Préparateur Mental, j'ai besoin de ...

Massothérapeute et préparateur mental indépendant, je recherche une carte de visite sobre et dynamique, sans images liées au massage ou à la préparation mentale mais intégrant mon logo. Les couleurs que j'aime bien sont : Blanc, gris, anthracite, noir et jaune

Contact Information for Business Card

carte de préférence Horizontale
neutre qui puisse toucher le deux domaines Massothérapie et préparation mentale

Requirements
Must have
• mon projet doit intégrer au recto:
LOGO
Loïc Bardèze
078 513 26 48
info@loicbardeze.ch
et éventuellement www.loicbardeze.ch

et au verso les deux adresses:

Chemin des Ormilles 7B
1436 Montchavel-le-Lac

Route de la Gravière 9
1700 Fribourg

Should not have
• mon projet ne doit pas contenir d'image en liens avec le massage ni la préparation mentale.

```html
<!DOCTYPE html>
<html lang="fr">
<head>
<meta charset="utf-8">
<title>Loïc Bardèze – Cartes de visite</title>
<link href="https://fonts.googleapis.com/css2?family=Montserrat:wght@400;500;600;700&display=swap" rel="stylesheet">
<style>
  :root {
    --bg: #e9e6e1;
    --steel-dark: #a8a8a8;
    --steel-mid: #c1c0c0;
    --steel-light: #b3b3b3;
    --silver-1: #ececec;
    --silver-2: #fbfbfb;
    --silver-3: #e2e2e2;
    --ink: #111111;
    --ink-soft: #2a2a2a;
    --accent: #8a5a2c;
  }
  * { box-sizing: border-box; margin: 0; padding: 0; }
  html, body { width: 1200px; height: 965px; overflow: hidden; }
  body {
    position: relative;
    background: var(--bg);
    font-family: "Montserrat", sans-serif;
    color: var(--ink);
  }
  .card {
    position: absolute;
    left: 278px;
    width: 647px;
    overflow: hidden;
  }
  .card::after {
    content: "";
    position: absolute; inset: 0;
    background: repeating-linear-gradient(150deg, rgba(255,255,255,0.07) 0 1px, rgba(0,0,0,0.03) 1px 3px);
    pointer-events: none;
  }
  .card--back {
    top: 98px; height: 368px;
    background: linear-gradient(150deg, var(--steel-dark) 0%, var(--steel-mid) 45%, var(--steel-light) 100%);
  }
  .card--front {
    top: 503px; height: 363px;
    background: linear-gradient(150deg, var(--silver-1) 0%, var(--silver-2) 40%, var(--silver-3) 70%, var(--silver-2) 100%);
  }
  .wordmark { position: absolute; z-index: 1; }
  .wordmark__name { font-weight: 700; color: var(--ink); letter-spacing: 0.5px; white-space: nowrap; }
  .wordmark__tagline { font-weight: 500; color: var(--ink); letter-spacing: 0.6px; text-transform: uppercase; white-space: nowrap; }
  .card--back .wordmark { left: 86px; top: 160px; }
  .card--back .wordmark__name { font-size: 36px; line-height: 40px; }
  .card--back .wordmark__tagline { font-size: 10.5px; margin-top: 4px; }
  .card--front .wordmark { left: 70px; top: 170px; }
  .card--front .wordmark__name { font-size: 25px; line-height: 28px; }
  .card--front .wordmark__tagline { font-size: 7.5px; margin-top: 3px; }

  .addresses { position: absolute; z-index: 1; top: 302px; left: 89px; display: flex; font-size: 15px; line-height: 20px; color: var(--ink-soft); }
  .address { width: 255px; white-space: nowrap; }
  .address--right { padding-left: 25px; }
  .addresses__divider { width: 2px; height: 34px; background: var(--ink-soft); margin-top: 2px; }

  .contact-divider { position: absolute; z-index: 1; left: 358px; top: 111px; width: 2px; height: 150px; background: var(--accent); }
  .person { position: absolute; z-index: 1; left: 374px; top: 118px; }
  .person__name { font-size: 24px; font-weight: 600; letter-spacing: 0.5px; color: var(--ink-soft); line-height: 28px; }
  .person__role { font-size: 14px; color: var(--ink-soft); margin-top: 1px; }
  .contacts { list-style: none; margin-top: 16px; }
  .contacts li { display: flex; align-items: center; font-size: 17px; line-height: 23.5px; color: var(--ink-soft); }
  .contacts svg { width: 15px; height: 15px; margin-right: 12px; fill: var(--ink-soft); flex: none; }
</style>
</head>
<body>
  <section class="card card--back" aria-label="Verso">
    <div class="wordmark">
      <div class="wordmark__name">Loïc Bardèze</div>
      <div class="wordmark__tagline">Massothérapeute / Préparateur Mental</div>
    </div>
    <div class="addresses">
      <p class="address">Chemin des Ormilles 7B<br>1436 Montchavel-le-Lac</p>
      <span class="addresses__divider"></span>
      <p class="address address--right">Route de la Gravière 9<br>1728 Corvanges</p>
    </div>
  </section>

  <section class="card card--front" aria-label="Recto">
    <div class="wordmark">
      <div class="wordmark__name">Loïc Bardèze</div>
      <div class="wordmark__tagline">Massothérapeute / Préparateur Mental</div>
    </div>
    <span class="contact-divider"></span>
    <div class="person">
      <div class="person__name">LOÏC BARDÈZE</div>
      <div class="person__role">Director</div>
      <ul class="contacts">
        <li><svg viewBox="0 0 24 24" aria-hidden="true"><path d="M6.6 10.8a15.2 15.2 0 0 0 6.6 6.6l2.2-2.2a1 1 0 0 1 1-.25 11.4 11.4 0 0 0 3.6.57 1 1 0 0 1 1 1V20a1 1 0 0 1-1 1A17 17 0 0 1 3 4a1 1 0 0 1 1-1h3.5a1 1 0 0 1 1 1c0 1.25.2 2.45.57 3.57a1 1 0 0 1-.25 1z"/></svg>078 513 26 48</li>
        <li><svg viewBox="0 0 24 24" aria-hidden="true"><path d="M2 5h20v2l-10 6L2 7zM2 9l10 6 10-6v10H2z"/></svg>info@loicbardeze.ch</li>
        <li><svg viewBox="0 0 24 24" aria-hidden="true"><circle cx="12" cy="12" r="10"/><path d="M2 12h20M12 2c3 3 3 17 0 20M12 2c-3 3-3 17 0 20" stroke="#fff" stroke-width="1.4" fill="none"/></svg>www.loicbardeze.ch</li>
      </ul>
    </div>
  </section>
</body>
</html>
```